Landing Page & Email Signature

I am looking for a new landing page as well as an email signature to align with the change in business. I have included the new logo/emblem which I'd like incorporated into the design and the current landing page is www.delmorquivex.com.au should you wish to see the old version.

```html
<!DOCTYPE html>
<html lang="en">
<head>
<meta charset="utf-8">
<title>Korrowa Transport</title>
<link href="https://fonts.googleapis.com/css2?family=Montserrat:wght@400;500;700&display=swap" rel="stylesheet">
<style>
  :root {
    --ink: #ffffff;
    --brand-red: #c8202f;
    --field-fill: rgba(255, 255, 255, 0.22);
    --field-line: rgba(255, 255, 255, 0.55);
    --photo-dark: #1c1c1d;
    --photo-mid: #3a3937;
    --photo-light: #4d4b47;
  }
  * { box-sizing: border-box; margin: 0; padding: 0; }
  html, body { width: 1200px; height: 667px; overflow: hidden; }
  body {
    font-family: "Montserrat", sans-serif;
    color: var(--ink);
    background: var(--photo-dark);
  }
  .landing {
    position: relative;
    width: 1200px;
    height: 667px;
    overflow: hidden;
  }
  .hero-photo {
    position: absolute;
    inset: 0;
    background:
      radial-gradient(ellipse 520px 300px at 560px 420px, rgba(70, 68, 64, 0.9), transparent 70%),
      radial-gradient(ellipse 420px 260px at 900px 380px, rgba(60, 58, 55, 0.8), transparent 70%),
      linear-gradient(180deg, #2a2a2b 0%, var(--photo-mid) 45%, var(--photo-light) 80%, #3b3936 100%);
  }
  .hero-photo::after {
    content: "";
    position: absolute;
    inset: 0;
    background: rgba(0, 0, 0, 0.35);
  }
  .about {
    position: absolute;
    left: 90px;
    top: 119px;
    width: 530px;
    font-size: 13.6px;
    line-height: 24.2px;
  }
  .about p + p { margin-top: 24.2px; }
  .guarantee {
    position: absolute;
    left: 90px;
    top: 411px;
    font-size: 15px;
    font-weight: 700;
  }
  .contact {
    position: absolute;
    left: 89px;
    top: 460px;
    font-size: 13.6px;
    line-height: 20.6px;
    list-style: none;
  }
  .brand {
    position: absolute;
    left: 790px;
    top: 110px;
    display: flex;
    align-items: center;
    gap: 10px;
  }
  .brand-dot {
    width: 22px;
    height: 22px;
    border-radius: 50%;
    background: var(--brand-red);
  }
  .brand-name {
    font-size: 26px;
    font-weight: 700;
    letter-spacing: 1px;
    color: var(--ink);
  }
  .enquiry {
    position: absolute;
    left: 682px;
    top: 223px;
    width: 429px;
  }
  .field {
    display: block;
    width: 429px;
    height: 35px;
    margin-bottom: 14px;
    background: var(--field-fill);
    border: 1px solid var(--field-line);
    padding: 0 17px;
    font-family: "Montserrat", sans-serif;
    font-size: 12.5px;
    letter-spacing: 1.1px;
    color: var(--ink);
  }
  .field::placeholder { color: var(--ink); opacity: 1; }
  .field-message {
    height: 125px;
    padding-top: 11px;
    resize: none;
  }
  .enquire-button {
    display: block;
    margin-top: 29px;
    width: 183px;
    height: 35px;
    background: var(--brand-red);
    border: 1px solid rgba(255, 255, 255, 0.6);
    color: var(--ink);
    font-family: "Montserrat", sans-serif;
    font-weight: 700;
    font-size: 18.5px;
    letter-spacing: 0.4px;
  }
  .copyright {
    position: absolute;
    left: 0;
    right: 0;
    top: 627px;
    text-align: center;
    font-size: 11.6px;
  }
</style>
</head>
<body>
<main class="landing">
  <div class="hero-photo" role="img" aria-label="Dark photograph of a black cruiser motorcycle parked on a gravel road with a hillside behind"></div>

  <section class="about">
    <p>Korrowa Transport was established in 2018 and transports motorcycles, motor bikes, ATVs and trikes as well as golf carts and buggies</p>
    <p>We weekly services to Sydney, Adelaide, Melbourne, Canberra and everywhere between as well as some inland routes, i.e. Dubbo Bathurst, Mudgee, Griffith, Wagga Wagga, Ballarat, Bendigo and Wangaratta.</p>
    <p>KorrowaTransport is a family owned and operated business based in the Sutherland Shire of Sydney. Our business offers an end to end solution and ensures you'll receive a personalised and face-to-face approach - this has always been and always will be our motto.</p>
  </section>

  <h2 class="guarantee">We Guarantee Your Satisfaction</h2>

  <ul class="contact">
    <li>Tobin Marlowe</li>
    <li>OWNER</li>
    <li>M. 0412 558730</li>
    <li>E. korrowatransport@mailbox.com</li>
    <li>www.delmorquivex.com.au</li>
  </ul>

  <div class="brand">
    <span class="brand-dot"></span>
    <span class="brand-name">KORROWA TRANSPORT</span>
  </div>

  <form class="enquiry">
    <input class="field" type="text" placeholder="Enter Your Name">
    <input class="field" type="tel" placeholder="Enter Your Phone Number">
    <input class="field" type="email" placeholder="Enter Your Email Adress">
    <textarea class="field field-message" placeholder="Enter Message"></textarea>
    <button class="enquire-button" type="button">ENQUIRE NOW</button>
  </form>

  <footer class="copyright">© Copyright 2020 Korrowa Transport &amp; Logistics | All Rights Reserved.</footer>
</main>
</body>
</html>
```